Brightwhisker Botanicals: Extracts for Pets

We need a brochure to help market the products. Brightwhisker Botanicals makes Chinese Herbal Extracts for cats and dogs. We have three products to launch with. An allergy, calming, and pain formula. They are based on traditional Chinese Medicine Formulas that have been used for hundreds of years on humans and animals. I would like the logo (attached) and have one or two cat/dogs pictures. They can be any of the pics from my website. Each product should have a descrition of what it treats (can pull from website). The brochure can highlight its convient, effective, and a safe alternative. It has to include:

This statement has not been evaluated by the KVQ.
This product is not intended to diagnose, treat, cure,
or prevent any disease. Brightwhisker is not liable for any adverse effects.

I included a sample with some of the important info for the products - the desing does not have to be similar, just an example of the copy

*I would like the format to be in Illustrator, vector, so that I can change sizes if I need to without loosing any detail.

Target Market(s)

Pet Owners

Industry/Entity Type

Pet Care

Font styles to use
Other font styles liked:
• Universal (as logo)

Requirements
Must have
• Logo, Description of each products.
Nice to have
• Dog or cat picture

```html
<!DOCTYPE html>
<html lang="en">
<head>
<meta charset="utf-8">
<title>Brightwhisker Botanicals – Brochure</title>
<link href="https://fonts.googleapis.com/css2?family=Lato:wght@300;400;700&family=Oswald:wght@400;500;700&display=swap" rel="stylesheet">
<style>
  :root {
    --green: #8cc63f;
    --green-dark: #3f7d2c;
    --lime: #a6d83a;
    --blue: #2c4f9e;
    --blue-deep: #1d3a80;
    --berry: #b3163f;
    --ink: #1e1e1e;
    --page-bg: #efefef;
    --white: #ffffff;
  }
  html, body {
    margin: 0;
    width: 1200px;
    height: 1200px;
    overflow: hidden;
    background: var(--page-bg);
  }
  .brochure-page {
    position: absolute;
    left: 243px;
    width: 714px;
    height: 548px;
    display: block;
  }
  .page-front { top: 32px; }
  .page-back { top: 616px; }
  .body-copy { font-family: "Lato", sans-serif; font-size: 14.5px; fill: var(--ink); }
  .intro-copy { font-family: "Lato", sans-serif; font-size: 13.5px; fill: var(--white); }
  .pill-label { font-family: "Oswald", sans-serif; font-weight: 500; font-size: 21px; fill: var(--white); }
  .cta-small { font-family: "Lato", sans-serif; font-weight: 700; font-size: 25px; fill: var(--ink); }
  .cta-big { font-family: "Oswald", sans-serif; font-weight: 700; font-size: 50px; fill: var(--ink); }
  .brand-name { font-family: "Lato", sans-serif; font-weight: 700; font-size: 19px; fill: var(--green-dark); }
  .web-address { font-family: "Lato", sans-serif; font-size: 19px; fill: var(--ink); }
  .section-title { font-family: "Lato", sans-serif; font-weight: 300; font-size: 34px; fill: var(--blue); }
  .quote-mark { font-family: "Lato", sans-serif; font-weight: 700; font-size: 30px; fill: var(--green); }
  .quote-copy { font-family: "Lato", sans-serif; font-size: 13.5px; fill: var(--ink); }
  .quote-author { font-family: "Lato", sans-serif; font-size: 14px; fill: var(--blue); }
  .footer-cta { font-family: "Lato", sans-serif; font-size: 18px; fill: var(--lime); }
  .footer-contact { font-family: "Lato", sans-serif; font-size: 17px; fill: var(--white); }
</style>
</head>
<body>

<!-- Front page -->
<svg class="brochure-page page-front" viewBox="0 0 840 645" xmlns="http://www.w3.org/2000/svg">
  <defs>
    <linearGradient id="front-bg" x1="0" y1="0" x2="0" y2="1">
      <stop offset="0" stop-color="#f7f7f7"/>
      <stop offset="1" stop-color="#d9d9d9"/>
    </linearGradient>
    <linearGradient id="meadow" x1="0" y1="0" x2="0" y2="1">
      <stop offset="0" stop-color="#9fb54a"/>
      <stop offset="0.5" stop-color="#b5b83c"/>
      <stop offset="1" stop-color="#c59a2c"/>
    </linearGradient>
    <radialGradient id="cta-fill" cx="0.4" cy="0.35" r="0.7">
      <stop offset="0" stop-color="#b8e34a"/>
      <stop offset="1" stop-color="#5fa62a"/>
    </radialGradient>
    <linearGradient id="band-blue" x1="0" y1="0" x2="0" y2="1">
      <stop offset="0" stop-color="#3459aa"/>
      <stop offset="1" stop-color="#1d3a80"/>
    </linearGradient>
    <linearGradient id="bottle-tones" x1="0" y1="0" x2="1" y2="0">
      <stop offset="0" stop-color="#5a1e16"/>
      <stop offset="0.5" stop-color="#6e2a1c"/>
      <stop offset="1" stop-color="#4e1414"/>
    </linearGradient>
  </defs>

  <rect class="page-surface" width="840" height="645" fill="url(#front-bg)"/>

  <!-- blue information band -->
  <path class="info-band-edge" d="M0,360 C160,410 330,440 470,420 C620,398 740,385 840,390 V645 H0 Z" fill="var(--green)"/>
  <path class="info-band" d="M0,378 C160,425 330,452 470,432 C620,410 740,398 840,402 V645 H0 Z" fill="url(#band-blue)"/>

  <!-- green web strip -->
  <path class="web-strip" d="M590,560 H840 V645 H560 C540,645 560,600 590,560 Z" fill="var(--lime)"/>
  <rect class="bottom-strip" x="0" y="630" width="840" height="15" fill="var(--lime)"/>

  <!-- puppy photo -->
  <path class="photo-edge" d="M0,0 H350 C420,90 465,210 448,305 L360,410 L0,375 Z" fill="var(--green)"/>
  <path class="hero-photo" role="img" aria-label="Photo of two black and white puppies sitting nose to nose in autumn grass"
        d="M0,0 H338 C404,90 448,210 432,300 L352,398 L0,362 Z" fill="url(#meadow)"/>

  <!-- call us today badge -->
  <circle cx="425" cy="340" r="86" fill="var(--white)"/>
  <circle cx="425" cy="340" r="77" fill="url(#cta-fill)"/>
  <text class="cta-small" x="423" y="331" text-anchor="middle">CALL US</text>
  <text class="cta-big" x="423" y="376" text-anchor="middle">TODAY</text>

  <!-- product headings -->
  <path d="M646,30 H840 V58 H646 Q633,58 633,44 Q633,30 646,30 Z" fill="var(--green-dark)"/>
  <text class="pill-label" x="736" y="52" text-anchor="middle">ALLERGIES &amp; ITCH</text>
  <text class="body-copy" x="805" y="82" text-anchor="end">Itching, Sinusitis, Red Eyes, Dermatitis, Eczema,</text>
  <text class="body-copy" x="805" y="102" text-anchor="end">Rash, Mucus</text>

  <path d="M473,118 H840 V146 H473 Q460,146 460,132 Q460,118 473,118 Z" fill="var(--blue)"/>
  <text class="pill-label" x="651" y="140" text-anchor="middle">PAIN: ANTI-INFLAMMATORY &amp; ANALGESIC</text>
  <text class="body-copy" x="798" y="175" text-anchor="end">Arthritis,Hip Dysplasia,ACL,Muscle and Joint</text>
  <text class="body-copy" x="798" y="195" text-anchor="end">Pain,Spinal Injury</text>

  <path d="M706,216 H840 V244 H706 Q693,244 693,230 Q693,216 706,216 Z" fill="var(--berry)"/>
  <text class="pill-label" x="770" y="238" text-anchor="middle">CALMING</text>
  <text class="body-copy" x="805" y="268" text-anchor="end">Anxiety, Hyperactivity, Trauma, Seizures,</text>
  <text class="body-copy" x="805" y="288" text-anchor="end">Hypertension, OCD</text>

  <!-- product bottles -->
  <rect class="product-shot" role="img" aria-label="Photo of three amber dropper bottles: pain relief, allergy and itch, and calming formulas"
        x="595" y="308" width="210" height="225" rx="14" fill="url(#bottle-tones)"/>

  <!-- logo panel -->
  <rect class="logo-panel" x="38" y="387" width="160" height="258" fill="var(--white)"/>
  <circle cx="118" cy="470" r="40" fill="var(--green)"/>
  <text class="brand-name" x="118" y="565" text-anchor="middle">Brightwhisker</text>
  <text class="brand-name" x="118" y="590" text-anchor="middle">Botanicals</text>

  <!-- intro copy -->
  <text class="intro-copy" x="545" y="464" text-anchor="end">Formulated by Licensed Herbalist trained in</text>
  <text class="intro-copy" x="545" y="481" text-anchor="end">Traditional Chinese Medicine. Extracts based on</text>
  <text class="intro-copy" x="545" y="498" text-anchor="end">formulas that have safely treated animals and</text>
  <text class="intro-copy" x="545" y="514" text-anchor="end">humans for over hundreds of years.</text>
  <text class="intro-copy" x="545" y="531" text-anchor="end">Testimonials at brightwhiskerbotanicals.com</text>

  <text class="intro-copy" x="545" y="565" text-anchor="end">This statement has not been evaluated by the KVQ.</text>
  <text class="intro-copy" x="545" y="582" text-anchor="end">This product is not intended to diagnose, treat, cure,</text>
  <text class="intro-copy" x="545" y="598" text-anchor="end">or prevent any disease. Brightwhisker is not liable</text>

  <text class="web-address" x="598" y="607">www.brightwhisker.co.uk</text>
</svg>

<!-- Back page -->
<svg class="brochure-page page-back" viewBox="0 0 840 645" xmlns="http://www.w3.org/2000/svg">
  <defs>
    <linearGradient id="back-bg" x1="0" y1="0" x2="0" y2="1">
      <stop offset="0" stop-color="#f8f8f8"/>
      <stop offset="1" stop-color="#dcdcdc"/>
    </linearGradient>
    <linearGradient id="dog-field" x1="0" y1="0" x2="0" y2="1">
      <stop offset="0" stop-color="#ffffff"/>
      <stop offset="0.3" stop-color="#ffffff"/>
      <stop offset="0.42" stop-color="#dbe6ee"/>
      <stop offset="0.62" stop-color="#c9c4b8"/>
      <stop offset="0.8" stop-color="#7f9a45"/>
      <stop offset="1" stop-color="#5b7d2e"/>
    </linearGradient>
    <linearGradient id="foot-blue" x1="0" y1="0" x2="0" y2="1">
      <stop offset="0" stop-color="#3459aa"/>
      <stop offset="1" stop-color="#1d3a80"/>
    </linearGradient>
  </defs>

  <rect class="page-surface" width="840" height="645" fill="url(#back-bg)"/>

  <!-- footer band -->
  <path class="footer-edge" d="M0,495 C180,520 380,505 560,445 V645 H0 Z" fill="var(--green)"/>
  <path class="footer-band" d="M0,510 C180,535 380,520 560,460 V645 H0 Z" fill="url(#foot-blue)"/>

  <!-- curved frame around dog photo -->
  <path d="M585,0 C612,150 560,290 500,390 C455,470 490,570 545,645 H840 V0 Z" fill="var(--blue-deep)"/>
  <path d="M598,0 C625,150 575,295 515,395 C472,472 505,570 558,645 H840 V0 Z" fill="var(--green)"/>
  <path class="hero-photo" role="img" aria-label="Photo of a fluffy white and brown dog in tall grass under a pale sky"
        d="M606,0 C633,150 585,298 527,398 C486,474 518,570 572,645 H840 V0 Z" fill="url(#dog-field)"/>

  <!-- logo -->
  <circle cx="712" cy="75" r="45" fill="var(--green)"/>
  <text class="brand-name" x="712" y="165" text-anchor="middle">Brightwhisker</text>
  <text class="brand-name" x="712" y="190" text-anchor="middle">Botanicals</text>

  <!-- testimonials -->
  <text class="section-title" x="42" y="62">Testimonials</text>

  <g class="testimonial">
    <text class="quote-mark" x="36" y="118">“</text>
    <text class="quote-copy" x="63" y="102">Mr Hadley has a Bulldog cross Rottweiler and following the trial he said</text>
    <text class="quote-copy" x="63" y="119">‘paw licking and scratching has stopped.’</text>
    <text class="quote-mark" x="316" y="138">”</text>
    <text class="quote-author" x="380" y="126">-Mr Hadley</text>
  </g>
  <line x1="36" y1="141" x2="535" y2="141" stroke="#d4d4d4" stroke-width="2"/>

  <g class="testimonial">
    <text class="quote-mark" x="36" y="193">“</text>
    <text class="quote-copy" x="63" y="177">Mr Pellow was amazed at how little he needed to feed and would definitely</text>
    <text class="quote-copy" x="63" y="194">continue to feed and recommend Brightwhisker.</text>
    <text class="quote-mark" x="368" y="210">”</text>
    <text class="quote-author" x="422" y="195">-Mr Pellow</text>
  </g>
  <line x1="36" y1="214" x2="530" y2="214" stroke="#d4d4d4" stroke-width="2"/>

  <g class="testimonial">
    <text class="quote-mark" x="36" y="265">“</text>
    <text class="quote-copy" x="63" y="249">Nora noticed an improvement in the coat of her Sprocker after</text>
    <text class="quote-copy" x="63" y="266">just a week.</text>
    <text class="quote-mark" x="140" y="283">”</text>
    <text class="quote-author" x="190" y="271">-Nora</text>
  </g>
  <line x1="36" y1="288" x2="500" y2="288" stroke="#d4d4d4" stroke-width="2"/>

  <g class="testimonial">
    <text class="quote-mark" x="36" y="331">“</text>
    <text class="quote-copy" x="63" y="315">Miss Wren and Bruno the Dogue de Bordeaux loved the</text>
    <text class="quote-copy" x="63" y="332">flavour and noticed a vast improvement in Bruno’s doggy</text>
    <text class="quote-copy" x="63" y="349">breath!</text>
    <text class="quote-mark" x="114" y="364">”</text>
    <text class="quote-author" x="151" y="352">-Miss Wren and Bruno</text>
  </g>
  <line x1="36" y1="374" x2="470" y2="374" stroke="#d4d4d4" stroke-width="2"/>

  <g class="testimonial">
    <text class="quote-mark" x="36" y="419">“</text>
    <text class="quote-copy" x="63" y="403">Ada’s Cavalier King Charles Spaniel preferred Brightwhisker</text>
    <text class="quote-copy" x="63" y="420">Paws to his normal food and Ada also said ‘eye staining</text>
    <text class="quote-copy" x="63" y="437">not as bad, dandruff also decreased’  so a happy 12 year</text>
    <text class="quote-copy" x="63" y="453">old Spaniel.</text>
    <text class="quote-mark" x="141" y="470">”</text>
    <text class="quote-author" x="184" y="458">-Ada’s Cavalier</text>
  </g>

  <!-- footer contact -->
  <text class="footer-cta" x="121" y="590" text-anchor="middle">CALL US TODAY</text>
  <text class="footer-contact" x="121" y="614" text-anchor="middle">+44 (0)116 496 0321</text>
  <line x1="227" y1="570" x2="227" y2="625" stroke="#4b6cb7" stroke-width="1.5"/>
  <text class="footer-contact" x="246" y="588">info@brightwhisker.co.uk</text>
  <text class="footer-contact" x="246" y="614">www.brightwhisker.co.uk</text>
</svg>

</body>
</html>
```